Brintel Works - Fast, Efficient and Gas Mainteance for Domestic, Commercial and Industrial clients

We are in the process of purchasing a new business and would like to get a new logo and business card.
Business is a gas maintenance business that also does new gas installations.
Has been established since 1988.
Services include:
Install all types of gas appliances & equipment inc. hot water units
Maintain / repair / replace all types of gas appliances & equipment

Target Market(s)

Domestic, Commercial and Industrial clients

Industry/Entity Type

Business

Contact Information for Business Card

admin@brintelworks.com.au
07 3918 4726
Brintel Works PTY LTD

Logo Text

Gas Fitting & Plumbing Maintenance Specialists

Font styles to use
Sans Serif

Requirements
Must have
• Logo
• Business name, contact number, email address, web address
• Domestic | Commercial | Industrial Est Since 1988
Nice to have
• Possibly a black card with a flame logo to one side
Should not have
• Spelling errors

```html
<!DOCTYPE html>
<html lang="en">
<head>
<meta charset="utf-8">
<title>Brintel Works – Business Cards</title>
<link rel="stylesheet" href="https://fonts.googleapis.com/css2?family=Quicksand:wght@400;500;600&display=swap">
<style>
  :root {
    --page-bg: #e4e2e0;
    --card-bg: #000000;
    --text-light: #d9d9d9;
    --text-muted: #bdbdbd;
    --accent: #f5a623;
    --mark-grey: #9a9a9a;
  }
  * { box-sizing: border-box; margin: 0; padding: 0; }
  html, body {
    width: 1200px;
    height: 1189px;
    overflow: hidden;
    background: var(--page-bg);
    font-family: "Quicksand", sans-serif;
  }
  .sheet {
    width: 1200px;
    height: 1189px;
    display: flex;
    flex-direction: column;
    align-items: center;
    justify-content: center;
    gap: 60px;
  }
  .card {
    width: 860px;
    height: 491px;
    background: var(--card-bg);
    color: var(--text-light);
    display: flex;
    flex-direction: column;
    align-items: center;
    justify-content: center;
    text-align: center;
    box-shadow: 0 8px 24px rgba(0,0,0,0.18);
  }
  .brand {
    display: flex;
    flex-direction: column;
    align-items: center;
    gap: 22px;
    margin-bottom: 30px;
  }
  .brand-dot {
    width: 92px;
    height: 92px;
    border-radius: 50%;
    background: var(--accent);
  }
  .brand-name {
    font-size: 34px;
    font-weight: 500;
    letter-spacing: 1px;
    color: var(--text-muted);
  }
  .services-title {
    font-size: 26px;
    font-weight: 500;
    letter-spacing: 1px;
    margin-bottom: 18px;
  }
  .services-list {
    list-style: none;
    font-size: 21px;
    font-weight: 400;
    line-height: 1.35;
    letter-spacing: 0.5px;
  }
  .employee-name {
    font-size: 34px;
    font-weight: 400;
    letter-spacing: 1px;
    margin-bottom: 14px;
  }
  .contact {
    list-style: none;
    font-size: 23px;
    font-weight: 400;
    line-height: 1.45;
    letter-spacing: 0.5px;
  }
  .contact-label {
    color: var(--accent);
    font-weight: 600;
  }
</style>
</head>
<body>
  <main class="sheet">
    <section class="card card-services">
      <div class="brand">
        <span class="brand-dot"></span>
        <span class="brand-name">Brintel Works PTY LTD</span>
      </div>
      <h2 class="services-title">SERVICES</h2>
      <ul class="services-list">
        <li>Install all types of gas appliances &amp; equipment inc hot water units</li>
        <li>Maintain / repair / replace all types of gas appliances &amp; equipment</li>
      </ul>
    </section>

    <section class="card card-contact">
      <div class="brand">
        <span class="brand-dot"></span>
        <span class="brand-name">Brintel Works PTY LTD</span>
      </div>
      <h2 class="employee-name">Employee Name</h2>
      <ul class="contact">
        <li><span class="contact-label">Phone:</span> 07 3918 4726</li>
        <li><span class="contact-label">Email:</span> admin@brintelworks.com.au</li>
      </ul>
    </section>
  </main>
</body>
</html>
```